brightquokka.net we need a webpage designed for our new product

We need a webpage designed for our new range of products from our new brand. We have had a logo designed on sketchharbor (see attached) and we want to keep to this theme. Our first product is a range of affordable app controlled LED lightbulbs.

I have added some photos that we think is good inspirational material and would be good as a background to this website, but we want the site to look modern but not conventional. We would like something that makes our company look quirky not corporate.

Thats it

Target Market(s)

Our product is being stocked by big name online retailers in the UK, the page will get link through hits from our app. Our target market is gadget freaks of all ages.

Industry/Entity Type

It Company

Requirements
Must have
• We are going to need a help page, text to be uploaded next few days.

We need a contact page.

design my work on iOS and Android as most people will access page through their handset or tablet.
Should not have
• We do not want anything too corporate.

```html
<!DOCTYPE html>
<html lang="en">
<head>
<meta charset="utf-8">
<title>brightquokka.net — App Controlled LED Lightbulbs</title>
<link href="https://fonts.googleapis.com/css2?family=Open+Sans:wght@400;600&family=Arimo:wght@400&display=swap" rel="stylesheet">
<style>
:root{
  --green:#3aa845;
  --green-dark:#2f8f3a;
  --nav:#5c5c5c;
  --page-bg:#5a5a5a;
  --footer:#4f4f4f;
  --ink:#333333;
  --body-ink:#555555;
  --muted:#c9c9c9;
  --white:#ffffff;
}
*{margin:0;padding:0;box-sizing:border-box}
html,body{width:811px;height:1200px;overflow:hidden}
body{position:relative;background:var(--page-bg);font-family:"Arimo",Arial,sans-serif;color:var(--ink)}
.abs{position:absolute}
.backdrop{left:0;top:0;width:811px;height:1200px;
  background:linear-gradient(180deg,#8a7a6e 0%,#8c7360 18%,#7a6e66 36%,#5d5d5d 60%,#575757 100%)}
.page{left:117px;top:39px;width:579px;height:1103px;background:linear-gradient(180deg,#ececec 0%,#f6f6f6 30%,#ffffff 50%)}

/* header */
.nav{left:253px;top:39px;width:443px;height:35px;background:var(--nav);display:flex;font-family:"Open Sans",sans-serif;font-size:8.5px;color:var(--white)}
.nav a{color:inherit;text-decoration:none;display:flex;align-items:center;justify-content:center;height:100%}
.nav .current{background:var(--green);width:66px;margin-left:71px}
.nav .item{padding:0 14px}
.logo-tab{left:117px;top:39px;width:136px;height:156px}
.logo-name{left:117px;top:150px;width:136px;text-align:center;font-family:"Open Sans",sans-serif;font-weight:600;font-size:9px;color:var(--green);letter-spacing:.3px}
.logo-dot{left:179px;top:118px;width:12px;height:12px;border-radius:50%;background:var(--green)}

/* hero */
.hero{left:118px;top:74px;width:577px;height:332px;border:2px solid var(--white);border-top:0;
  background:radial-gradient(ellipse at 75% 55%,#e8d6c8 0%,#c9a88f 22%,#8a5f43 50%,#5a3b2a 80%);}
.caption{left:262px;top:361px;width:330px;height:44px;background:rgba(60,60,60,.85);color:var(--white);
  font-family:"Open Sans",sans-serif;font-size:18px;display:flex;align-items:center;justify-content:center}
.arrow{width:19px;height:19px;top:373px}

/* features */
.thumb{width:173px;height:117px;top:427px;background:var(--white);padding:3px;box-shadow:0 0 3px rgba(0,0,0,.25)}
.thumb div{width:100%;height:100%}
.t1{background:linear-gradient(135deg,#7a5a48,#b08a6e 45%,#8a4a3f)}
.t2{background:linear-gradient(135deg,#3b4c8a,#b23a3a 50%,#d6c4a0)}
.t3{background:linear-gradient(135deg,#2d6fb5 0%,#e2a12a 45%,#7a4a22 100%)}
.feature-title{top:560px;font-size:10.5px;color:var(--ink)}
.copy{font-size:6.6px;line-height:12.8px;color:var(--body-ink);text-align:justify;width:175px}
.feature-copy{top:584px}

.section-bar{left:134px;top:663px;width:546px;height:24px;background:linear-gradient(180deg,#6a6a6a,#4f4f4f);
  border-radius:2px;color:var(--white);font-family:"Open Sans",sans-serif;font-size:10.5px;padding-left:12px;display:flex;align-items:center}

/* products */
.product-img{top:710px;width:174px;height:148px;border:1px solid #e2e2e2}
.p1{background:radial-gradient(circle at 50% 35%,#d9d9d9,#9a9a9a 35%,#f6f6f6 60%)}
.p2{background:radial-gradient(circle at 60% 50%,#9a9a9a,#d6d6d6 45%,#ededed)}
.p3{background:radial-gradient(circle at 40% 50%,#ffffff,#e4e4e4 40%,#f2f2f2)}
.product-title{top:868px;font-family:"Open Sans",sans-serif;font-size:9.5px;color:var(--ink)}
.product-copy{top:886px;font-size:6.4px;line-height:14.4px}
.btn{top:934px;width:46px;height:18px;background:var(--green);color:var(--white);font-family:"Open Sans",sans-serif;
  font-size:8px;display:flex;align-items:center;padding-left:8px;gap:10px}

/* footer */
.footer{left:117px;top:980px;width:579px;height:162px;background:var(--footer)}
.footer-head{top:996px;font-family:"Open Sans",sans-serif;font-size:10px;color:var(--muted)}
.links{left:134px;top:1030px;font-family:"Open Sans",sans-serif;font-size:6.6px;line-height:12.8px;color:var(--muted);list-style:none}
.addr{font-family:"Open Sans",sans-serif;font-size:8px;line-height:12.8px;color:var(--muted)}
.news-copy{left:501px;top:1030px;width:180px;font-family:"Open Sans",sans-serif;font-size:6.4px;line-height:12.8px;color:var(--muted)}
.email-field{left:501px;top:1080px;width:127px;height:30px;background:var(--white);font-family:"Open Sans",sans-serif;font-size:7px;color:#333;padding-left:7px;display:flex;align-items:center}
.signup{left:628px;top:1080px;width:50px;height:30px;background:var(--green-dark);color:var(--white);font-family:"Open Sans",sans-serif;font-size:11px;display:flex;align-items:center;justify-content:center}
.copyright{left:116px;top:1169px;font-size:6.6px;color:#e6e6e6}
.social{width:15px;height:15px;border-radius:50%;background:#f2f2f2;top:1164px}
</style>
</head>
<body>
<div class="abs backdrop" role="img" aria-label="Blurred photo of a shop shelf with cartoon-cat figurines"></div>
<div class="abs page"></div>

<svg class="abs logo-tab" viewBox="0 0 136 156" aria-hidden="true"><polygon points="0,0 136,0 136,154 0,156 0,0" fill="#fff"/><polygon points="0,156 136,154 136,150" fill="#e5e5e5"/></svg>
<div class="abs logo-dot"></div>
<div class="abs logo-name">BRIGHTQUOKKA</div>

<nav class="abs nav">
  <a class="current" href="#">HOME</a>
  <a class="item" href="#" style="padding-left:20px">About Us</a>
  <a class="item" href="#" style="padding-left:20px">Our Products</a>
  <a class="item" href="#" style="padding-left:20px">Blog</a>
  <a class="item" href="#" style="padding-left:24px">Contact us</a>
</nav>

<div class="abs hero" role="img" aria-label="Close-up of a white ceramic lamp on a wooden table in a warm, blurred shop"></div>
<div class="abs caption">Range of affordable app controlled</div>
<svg class="abs arrow" style="left:252px" viewBox="0 0 20 20"><circle cx="10" cy="10" r="9.5" fill="#e8e8e8"/><path d="M11.5 6.5 8 10l3.5 3.5" stroke="#777" stroke-width="1.6" fill="none"/></svg>
<svg class="abs arrow" style="left:582px" viewBox="0 0 20 20"><circle cx="10" cy="10" r="9.5" fill="#e8e8e8"/><path d="M8.5 6.5 12 10l-3.5 3.5" stroke="#777" stroke-width="1.6" fill="none"/></svg>

<div class="abs thumb" style="left:134px"><div class="t1" role="img" aria-label="Busy antique market hall"></div></div>
<div class="abs thumb" style="left:320px"><div class="t2" role="img" aria-label="Pile of colourful toys"></div></div>
<div class="abs thumb" style="left:506px"><div class="t3" role="img" aria-label="Row of cartoon-cat telephone figurines"></div></div>

<h3 class="abs feature-title" style="left:134px;font-weight:400">Qui officia deserunt mollit an</h3>
<h3 class="abs feature-title" style="left:320px;font-weight:400">Excepteur sint occaecat cupidatat</h3>
<h3 class="abs feature-title" style="left:505px;font-weight:400">Lorem ipsum dolor sit</h3>
<p class="abs copy feature-copy" style="left:134px">Lorem ipsum dolor sit amet, consectetur adipiscing elit. Morbi eu neque sed urna accumsan gravida. Pellentesque habitant morbi tristique senectus et netus et malesuada fames ac turpis egestas.Lorem ipsum dolor sit amet, consectetur adipiscing elit.</p>
<p class="abs copy feature-copy" style="left:319px">Lorem ipsum dolor sit amet, consectetur adipiscing elit. Morbi eu neque sed urna accumsan gravida. Pellentesque habitant morbi tristique senectus et netus et malesuada fames ac turpis egestas.Lorem ipsum dolor sit amet, consectetur adipiscing elit.</p>
<p class="abs copy feature-copy" style="left:505px">Lorem ipsum dolor sit amet, consectetur adipiscing elit. Morbi eu neque sed urna accumsan gravida. Pellentesque habitant morbi tristique senectus et netus et malesuada fames ac turpis egestas.Lorem ipsum dolor sit amet, consectetur adipiscing elit.</p>

<div class="abs section-bar">New Products</div>

<div class="abs product-img p1" style="left:135px" role="img" aria-label="Silver LED spotlight bulb with many lenses"></div>
<div class="abs product-img p2" style="left:319px" role="img" aria-label="Two small LED spot bulbs"></div>
<div class="abs product-img p3" style="left:505px" role="img" aria-label="White frosted LED bulb"></div>

<h3 class="abs product-title" style="left:135px;font-weight:400">Controlled LED lightbulbs</h3>
<h3 class="abs product-title" style="left:319px;font-weight:400">LED LIGHT BULBS</h3>
<h3 class="abs product-title" style="left:505px;font-weight:400">Lumora Launches First 100 Watt</h3>
<p class="abs copy product-copy" style="left:135px">Lorem ipsum dolor sit amet, consectetur adipiscing elit. Sed blandit massa vel mauris sollicitudin dignissim. Phasellus ultrices tellus eget ipsum ornare</p>
<p class="abs copy product-copy" style="left:319px">Lorem ipsum dolor sit amet, consectetur adipiscing elit. Sed blandit massa vel mauris sollicitudin dignissim. Phasellus ultrices tellus eget ipsum ornare</p>
<p class="abs copy product-copy" style="left:505px">Lorem ipsum dolor sit amet, consectetur adipiscing elit. Sed blandit massa vel mauris sollicitudin dignissim. Phasellus ultrices tellus eget ipsum ornare</p>
<a class="abs btn" style="left:135px">View <span>›</span></a>
<a class="abs btn" style="left:319px">View <span>›</span></a>
<a class="abs btn" style="left:505px">View <span>›</span></a>

<footer class="abs footer"></footer>
<h4 class="abs footer-head" style="left:134px;font-weight:400">QUICK LINKS</h4>
<h4 class="abs footer-head" style="left:306px;font-weight:400">ADDRESS</h4>
<h4 class="abs footer-head" style="left:501px;font-weight:400">NEWSLETTER</h4>
<ul class="abs links">
  <li>HOME</li><li>ADMISSIONS</li><li>ABOUT US</li><li>OUR PRODUCTS</li><li>BLOG</li><li>CONTACT</li><li>LED LIGHTBULBS</li>
</ul>
<svg class="abs" style="left:307px;top:1030px" width="10" height="16" viewBox="0 0 10 16"><path d="M5 1a4 4 0 0 0-4 4c0 3 4 9 4 9s4-6 4-9a4 4 0 0 0-4-4z" fill="#222"/><circle cx="5" cy="5" r="1.5" fill="#4f4f4f"/></svg>
<p class="abs addr" style="left:329px;top:1030px">512 Lanternfield Street<br>Millbrook, VA 23999,<br>United States</p>
<svg class="abs" style="left:308px;top:1076px" width="9" height="16" viewBox="0 0 9 16"><rect x="0.5" y="0.5" width="8" height="15" rx="1.5" fill="#222"/><rect x="1.8" y="2.5" width="5.4" height="9" fill="#4f4f4f"/></svg>
<p class="abs addr" style="left:331px;top:1078px">Call us: +1 555-014-2290</p>
<svg class="abs" style="left:306px;top:1112px" width="14" height="10" viewBox="0 0 14 10"><rect width="14" height="10" fill="#222"/><path d="M0 0l7 5 7-5" stroke="#4f4f4f" fill="none"/></svg>
<p class="abs addr" style="left:330px;top:1110px">info@brightquokka.net</p>
<p class="abs news-copy">Excepteur sint occaecat cupidatat non proident, sunt in culpa qui officia deserunt mollit anim id est laborum.</p>
<div class="abs email-field">Enter Email</div>
<div class="abs signup">Sign Up</div>

<p class="abs copyright">Copyright © 2014 brightquokka.net . All rights reserved.</p>
<span class="abs social" style="left:621px"></span>
<span class="abs social" style="left:641px"></span>
<span class="abs social" style="left:661px"></span>
<span class="abs social" style="left:681px"></span>
</body>
</html>
```